Verodex business card

Business card for sustainable investment company called "Verodex". Verodex is an exchange platform selling carbon credits between buyers and sellers. Carbon Credits are an environmental commodity for reducing global carbon emissions.

the card should obviously have our logo and the theme should be sustainability/environment mixed with a trading platform.

Contact Information for Business Card

Logo, Name, Title, Phone, Email

Colors
0054AA
0677BA
7BADD7
CADEEF
E8F1F8
0094D4
00A9DD
6FCCEA
C7EBF8
E9F6FB
00AB8E
00BBA5
67D7C9
C6EFE9
E9F9F6
59FF00
82FF00
B8FF75
E3FFCB
F4FFEA

```html
<!DOCTYPE html>
<html lang="en">
<head>
<meta charset="utf-8">
<title>Verodex business cards</title>
<link rel="stylesheet" href="https://fonts.googleapis.com/css2?family=Archivo+Black&family=Roboto:wght@400;500&family=Montserrat:wght@500&display=swap">
<style>
  :root {
    --backdrop: #ababab;
    --divider: #cfcfcf;
    --card-front: #e9f6fb;
    --card-back: #0054aa;
    --ink: #0054aa;
    --ink-soft: #0677ba;
    --accent: #00ab8e;
    --back-text: #e9f6fb;
    --back-mark: #59ff00;
    --card-shadow: rgba(0,0,0,0.28);
  }
  * { box-sizing: border-box; margin: 0; padding: 0; }
  html, body { width: 1200px; height: 4121px; overflow: hidden; }
  body {
    background: var(--backdrop);
    display: grid;
    grid-template-rows: repeat(5, 1fr);
    font-family: "Roboto", Arial, sans-serif;
    color: var(--ink);
  }
  .card-set { position: relative; border-top: 3px solid var(--divider); }
  .card-set:first-child { border-top: none; }
  .card {
    position: absolute;
    width: 560px;
    height: 320px;
    border-radius: 3px;
    box-shadow: 0 24px 40px var(--card-shadow);
  }
  .card-front { left: 220px; top: 90px; background: var(--card-front); }
  .card-back  { left: 440px; top: 440px; background: var(--card-back); }

  .front-brand {
    position: absolute; right: 44px; top: 44px;
    font-family: "Montserrat", Arial, sans-serif; font-weight: 500;
    font-size: 20px; letter-spacing: 1px; text-transform: uppercase;
    color: var(--ink);
  }
  .identity {
    position: absolute; right: 290px; top: 146px; text-align: right;
  }
  .person-name {
    font-family: "Archivo Black", "Arial Black", sans-serif;
    font-size: 22px; text-transform: uppercase; letter-spacing: 0.3px; line-height: 1.1;
    color: var(--ink);
  }
  .person-title { font-size: 14px; font-weight: 500; margin-top: 4px; color: var(--ink-soft); }
  .rule {
    position: absolute; left: 282px; top: 146px;
    width: 2px; height: 58px; background: var(--accent);
  }
  .contact {
    position: absolute; left: 300px; top: 148px;
    font-size: 15px; font-weight: 500; line-height: 1.3; list-style: none;
    color: var(--ink-soft);
  }
  .back-brand {
    position: absolute; inset: 0;
    display: flex; align-items: center; justify-content: center; gap: 22px;
  }
  .back-mark { width: 70px; height: 70px; border-radius: 50%; background: var(--back-mark); }
  .back-name {
    font-family: "Montserrat", Arial, sans-serif; font-weight: 500;
    font-size: 56px; letter-spacing: 2px; text-transform: uppercase;
    color: var(--back-text);
  }
</style>
</head>
<body>

<section class="card-set">
  <div class="card card-front">
    <div class="front-brand">Verodex</div>
    <div class="identity"><div class="person-name">Elian Moravec</div><div class="person-title">Founder</div></div>
    <div class="rule"></div>
    <ul class="contact"><li>4805550172</li><li>elian@verodex.com</li><li>verodex.com</li></ul>
  </div>
  <div class="card card-back"><div class="back-brand"><span class="back-mark"></span><span class="back-name">Verodex</span></div></div>
</section>

<section class="card-set">
  <div class="card card-front">
    <div class="front-brand">Verodex</div>
    <div class="identity"><div class="person-name">Tal Renner</div><div class="person-title">Founder</div></div>
    <div class="rule"></div>
    <ul class="contact"><li>+36305550148</li><li>tal@verodex.com</li><li>verodex.com</li></ul>
  </div>
  <div class="card card-back"><div class="back-brand"><span class="back-mark"></span><span class="back-name">Verodex</span></div></div>
</section>

<section class="card-set">
  <div class="card card-front">
    <div class="front-brand">Verodex</div>
    <div class="identity"><div class="person-name">Oren Kessel</div><div class="person-title">Founder</div></div>
    <div class="rule"></div>
    <ul class="contact"><li>+86 135 5501 2974</li><li>oren@verodex.com</li><li>verodex.com</li></ul>
  </div>
  <div class="card card-back"><div class="back-brand"><span class="back-mark"></span><span class="back-name">Verodex</span></div></div>
</section>

<section class="card-set">
  <div class="card card-front">
    <div class="front-brand">Verodex</div>
    <div class="identity"><div class="person-name">Nikos Veridis</div><div class="person-title">Founder</div></div>
    <div class="rule"></div>
    <ul class="contact"><li>+36 30 555 0261</li><li>nikos@verodex.com</li><li>verodex.com</li></ul>
  </div>
  <div class="card card-back"><div class="back-brand"><span class="back-mark"></span><span class="back-name">Verodex</span></div></div>
</section>

<section class="card-set">
  <div class="card card-front">
    <div class="front-brand">Verodex</div>
    <div class="identity"><div class="person-name">Clara Deveaux</div><div class="person-title">Vice President</div></div>
    <div class="rule"></div>
    <ul class="contact"><li>+33 6 55 50 19 42</li><li>cd@verodex.com</li><li>verodex.com</li></ul>
  </div>
  <div class="card card-back"><div class="back-brand"><span class="back-mark"></span><span class="back-name">Verodex</span></div></div>
</section>

</body>
</html>
```